Brackenford Fluidworks needs a website describing the repair business we are in.

Brackenford Fluidworks is a full hydraulic repair facility. We have 2 shops. We repair and service all hydraulic cylinders, pneumatic cylinders, hydraulic pumps, motors, valves and gearboxes. Our services range from large industrial plants to the individual that owns one piece of equipment. We also offer removal and install of cylinders. Along with free pick up and delivery, within a certain distance which is usually 100 miles from one of our shops.

With over 30 years experience in the hydraulic business, we can repair or replace any job. There is not a job too big or too small, we service them all.

We have customers that send whole pieces of equipment to us to do complete overhauls on all the hydraulics. Ranging from a country club green roller to a 10 ton boom truck.

Target Market(s)

Industrial plants, road builders, dirt work companies, general contractors, owners of industrial equipment (bulldozers, excavators, loaders, scrapers, motor graders, etc.

Industry/Entity Type

Hydraulic

Number of Pages Required

5+ page

Font styles to use
Sans Serif

Colors
ec1f27
ffffff
aaaaaa

Requirements
Must have
• Information about what we offer and pictures of jobs completed.
Nice to have
• Nice stock photos of jobsites and industrial plants.
Should not have
• Any sort of comical characters.

```html
<!DOCTYPE html>
<html lang="en">
<head>
<meta charset="utf-8">
<title>Brackenford Fluidworks — Hydraulic Repair</title>
<link href="https://fonts.googleapis.com/css2?family=Poppins:wght@400;500;600&family=Open+Sans:wght@400;600&display=swap" rel="stylesheet">
<style>
:root{
  --red:#ec1f27;
  --red-dark:#c8101a;
  --white:#ffffff;
  --grey:#aaaaaa;
  --grey-mid:#8f8f8f;
  --grey-light:#ececec;
  --panel:#f1f1f1;
  --ink:#111111;
  --text:#333333;
  --black:#0c0c0c;
  --head:"Poppins",sans-serif;
  --body:"Open Sans",sans-serif;
}
*{box-sizing:border-box;margin:0;padding:0}
html,body{width:1200px;height:3346px;overflow:hidden;background:var(--white)}
body{position:relative;font-family:var(--body);color:var(--text)}
a{color:inherit;text-decoration:none}

/* header */
.site-header{position:absolute;top:0;left:0;width:1200px;height:123px;background:var(--white)}
.brand{position:absolute;left:98px;top:14px;display:flex;flex-direction:column;align-items:center;gap:6px;width:130px}
.brand-dot{width:60px;height:60px;border-radius:50%;background:var(--red)}
.brand-name{font-family:var(--head);font-weight:600;font-size:13px;line-height:1.15;color:var(--red);text-align:center;letter-spacing:.5px}
.register{position:absolute;right:100px;top:16px;height:38px;display:flex;font-family:var(--head);font-weight:600;font-size:13px;color:var(--white);border-radius:4px;overflow:hidden}
.register-icon{width:38px;background:var(--grey-mid);display:flex;align-items:center;justify-content:center}
.register-label{background:var(--red);padding:0 14px;display:flex;align-items:center}
.main-nav{position:absolute;right:100px;top:72px;display:flex;gap:38px;font-family:var(--head);font-weight:500;font-size:15px;color:var(--ink)}
.main-nav .current{color:var(--red)}

/* hero */
.hero{position:absolute;top:123px;left:0;width:1200px;height:535px;
  background:linear-gradient(100deg,#2a2a30 0%,#8a5a2a 18%,#e09030 30%,#6a4a38 45%,#2e3e52 62%,#4e6a80 80%,#24303e 100%)}
.hero-shade{position:absolute;inset:0;background:linear-gradient(180deg,rgba(10,14,20,.35),rgba(10,14,20,.15) 50%,rgba(10,14,20,.55))}
.hero-copy{position:absolute;left:90px;top:140px;width:550px;text-align:center;color:var(--white)}
.hero-title{font-family:var(--head);font-weight:500;font-size:38px;letter-spacing:.5px}
.hero-sub{font-family:var(--head);font-weight:600;font-size:23px;line-height:34px;margin-top:18px}
.btn{display:inline-flex;height:38px;border-radius:4px;overflow:hidden;font-family:var(--head);font-weight:600;font-size:14px;color:var(--white)}
.btn-label{background:var(--red);padding:0 10px;display:flex;align-items:center}
.btn-arrow{width:34px;background:var(--grey-mid);display:flex;align-items:center;justify-content:center}
.hero .btn{margin-top:18px}
.hero-dots{position:absolute;left:563px;top:490px;display:flex;gap:6px}
.hero-dots span{width:14px;height:14px;border-radius:50%;border:2px solid var(--white)}
.hero-dots .on{background:var(--red);border-color:var(--red)}

/* welcome */
.section-title{font-family:var(--head);font-weight:500;font-size:36px;color:var(--ink);text-align:center;letter-spacing:.3px}
.welcome{position:absolute;top:658px;left:0;width:1200px;height:513px}
.welcome .section-title{margin-top:68px}
.welcome-intro{width:820px;margin:22px auto 0;text-align:center;font-size:14px;line-height:26px;color:var(--text)}
.service-card{position:absolute;top:247px;width:480px;height:182px;background:var(--panel);border:1px solid #d6d6d6;box-shadow:0 3px 3px rgba(0,0,0,.25)}
.service-card.left{left:98px}.service-card.right{left:620px}
.service-icon{position:absolute;left:34px;top:16px;width:84px;height:84px;border-radius:50%;background:var(--grey-mid);display:flex;align-items:center;justify-content:center}
.service-name{position:absolute;left:136px;top:24px;font-family:var(--head);font-weight:500;font-size:22px;line-height:30px;color:var(--ink)}
.service-text{position:absolute;left:34px;right:34px;top:112px;font-size:13.5px;line-height:24px;color:var(--text)}

/* stats */
.stats{position:absolute;top:1171px;left:0;width:1200px;height:272px;
  background:linear-gradient(90deg,#4a1e26,#6e2a35 30%,#8a3a42 60%,#5a2430)}
.stats-shade{position:absolute;inset:0;background:rgba(110,20,35,.35)}
.stats-row{position:absolute;left:80px;top:85px;width:1040px;display:flex}
.stat{flex:1;text-align:center;color:var(--white);position:relative}
.stat+.stat::before{content:"";position:absolute;left:0;top:6px;height:90px;width:1px;background:rgba(255,255,255,.7)}
.stat svg{display:block;margin:0 auto 10px}
.stat-big{font-family:var(--head);font-weight:500;font-size:24px}
.stat-small{font-family:var(--head);font-size:17px}

/* about */
.about{position:absolute;top:1443px;left:0;width:1200px;height:587px}
.about .section-title{margin-top:82px}
.about-tag{text-align:center;font-family:var(--head);font-weight:500;font-size:17px;color:var(--ink);margin-top:12px}
.about-copy{position:absolute;left:100px;top:210px;width:462px;font-size:14px;line-height:27px}
.about-copy p+p{margin-top:20px}
.about-copy .btn{margin-top:16px}
.about-photo{position:absolute;left:600px;top:200px;width:502px;height:298px;border:3px solid var(--white);box-shadow:0 0 0 1px #dddddd;
  background:linear-gradient(120deg,#caa838,#8a8468 35%,#d0642a 55%,#7a8890 75%,#d8c040)}

/* testimonials */
.testimonials{position:absolute;top:2030px;left:0;width:1200px;height:446px;background:var(--grey-light)}
.testimonials .section-title{margin-top:72px}
.quote-card{position:absolute;top:182px;width:480px;height:181px;background:var(--panel);border:1px solid #d4d4d4}
.quote-card.left{left:98px}.quote-card.right{left:620px}
.quote-badge{position:absolute;left:50%;top:-46px;margin-left:-42px;width:84px;height:84px;border-radius:50%;background:var(--panel);border:4px solid var(--white);display:flex;align-items:center;justify-content:center;font-family:var(--head);font-weight:600;font-size:64px;line-height:1;color:var(--red);padding-top:26px}
.quote-text{position:absolute;left:34px;right:34px;top:54px;text-align:center;font-style:italic;font-size:15.5px;line-height:27px;color:var(--ink)}
.quote-name{position:absolute;right:30px;bottom:18px;font-family:var(--head);font-weight:500;font-size:19px;color:var(--red)}
.slide-arrow{position:absolute;top:246px}
.slide-arrow.prev{left:36px}.slide-arrow.next{right:36px}

/* newsletter */
.newsletter{position:absolute;top:2476px;left:0;width:1200px;height:495px;
  background:linear-gradient(90deg,#1a2226,#3a464c 25%,#565e62 50%,#3e484c 75%,#1c2428)}
.newsletter-shade{position:absolute;inset:0;background:rgba(0,0,0,.35)}
.newsletter-box{position:absolute;left:285px;top:120px;width:630px;height:288px;background:var(--white);border-radius:10px}
.mail-badge{position:absolute;left:50%;top:-46px;margin-left:-46px;width:92px;height:92px;border-radius:50%;background:var(--white);border:4px solid var(--red);display:flex;align-items:center;justify-content:center}
.mail-badge span{width:72px;height:72px;border-radius:50%;background:var(--red);display:flex;align-items:center;justify-content:center}
.newsletter-title{position:absolute;left:0;right:0;top:78px;text-align:center;font-family:var(--head);font-weight:500;font-size:34px;color:var(--ink)}
.newsletter-form{position:absolute;left:47px;top:142px;width:536px;height:45px;display:flex;border-radius:4px;overflow:hidden}
.newsletter-input{flex:1;background:var(--red);color:var(--white);font-size:13px;display:flex;align-items:center;padding-left:10px}
.newsletter-submit{width:116px;background:var(--grey-mid);color:var(--red);font-family:var(--head);font-weight:600;font-size:18px;display:flex;align-items:center;justify-content:center;gap:8px}
.newsletter-check{position:absolute;left:38px;top:212px;font-size:15px;color:var(--ink);display:flex;align-items:center;gap:6px}

/* footer */
.site-footer{position:absolute;top:2971px;left:0;width:1200px;height:308px;background:var(--grey-light)}
.footer-brand{position:absolute;left:96px;top:80px;width:200px;display:flex;flex-direction:column;align-items:center;gap:10px}
.footer-brand .brand-dot{width:96px;height:96px}
.footer-brand .brand-name{font-size:20px}
.footer-col{position:absolute;top:64px}
.footer-col h3{font-family:var(--head);font-weight:500;font-size:18px;color:var(--ink);margin-bottom:24px}
.footer-col li{list-style:none;font-size:13px;line-height:28px;color:var(--ink)}
.col-links{left:413px}.col-res{left:660px}.col-connect{left:897px}
.socials{display:flex;gap:6px}
.socials span{width:46px;height:46px;border-radius:6px;background:var(--grey-mid)}
.copyright{position:absolute;top:3279px;left:0;width:1200px;height:67px;background:var(--black);color:var(--white);font-size:13px;display:flex;align-items:center;justify-content:center}
</style>
</head>
<body>

<header class="site-header">
  <a class="brand" href="#"><span class="brand-dot"></span><span class="brand-name">BRACKENFORD FLUIDWORKS</span></a>
  <a class="register" href="#">
    <span class="register-icon"><svg width="16" height="16" viewBox="0 0 16 16"><circle cx="8" cy="5" r="3.5" fill="#ec1f27"/><path d="M1 16c0-4 3-6 7-6s7 2 7 6z" fill="#ec1f27"/></svg></span>
    <span class="register-label">REGISTER</span>
  </a>
  <nav class="main-nav">
    <a class="current" href="#">HOME</a><a href="#">ABOUT US</a><a href="#">SERVICES</a><a href="#">PROJECTS</a><a href="#">BLOG</a><a href="#">CONTACT</a>
  </nav>
</header>

<section class="hero" role="img" aria-label="Industrial plant with pipework and a tank at sunset">
  <div class="hero-shade"></div>
  <div class="hero-copy">
    <h1 class="hero-title">BRACKENFORD FLUIDWORKS</h1>
    <p class="hero-sub">Sed Ut Perspiciatis Unde Omnis Iste Natus Error Sit Voluptatem Accustium Doloremque Laudantium</p>
    <a class="btn" href="#"><span class="btn-label">READ MORE</span><span class="btn-arrow"><svg width="18" height="18" viewBox="0 0 18 18"><circle cx="9" cy="9" r="9" fill="#ec1f27"/><path d="M7 5l4 4-4 4" stroke="#fff" stroke-width="2" fill="none"/></svg></span></a>
  </div>
  <div class="hero-dots"><span class="on"></span><span></span><span></span><span></span></div>
</section>

<section class="welcome">
  <h2 class="section-title">WELCOME TO BRACKENFORD FLUIDWORKS</h2>
  <p class="welcome-intro">Nam libero tempore, cum soluta nobis est eligendi optio cumque nihil impedit quo minus id quod maxime placeat facere possimus, omnis voluptas assumenda est, omnis dolor repellendus. Temporibus autem quibusdam et aut officiis debitis aut rerum necessitatibus saepe eveniet ut et voluptates repudiandae sint et molestiae non recusandae.</p>
  <article class="service-card left">
    <div class="service-icon"><svg width="44" height="44" viewBox="0 0 44 44"><rect x="4" y="26" width="36" height="14" rx="2" fill="none" stroke="#ec1f27" stroke-width="3"/><path d="M22 4v18M15 15l7 7 7-7" stroke="#ec1f27" stroke-width="3" fill="none"/></svg></div>
    <h3 class="service-name">Installation &amp; Removal<br>Of Cylinders</h3>
    <p class="service-text">At vero eos et accusamus et iusto odio dignissimos ducimus qui iti atque corrupti quos dostias excepturi sint.</p>
  </article>
  <article class="service-card right">
    <div class="service-icon"><svg width="44" height="44" viewBox="0 0 44 44"><path d="M8 8l28 28M36 8L8 36" stroke="#ec1f27" stroke-width="5" stroke-linecap="round"/></svg></div>
    <h3 class="service-name">Repairing &amp; Servicing<br>Of Cylinders</h3>
    <p class="service-text">At vero eos et accusamus et iusto odio dignissimos ducimus qui iti atque corrupti quos dostias excepturi sint.</p>
  </article>
</section>

<section class="stats" role="img" aria-label="Hydraulic equipment trailer at a work yard">
  <div class="stats-shade"></div>
  <div class="stats-row">
    <div class="stat"><svg width="40" height="34" viewBox="0 0 40 34"><rect x="2" y="8" width="36" height="24" rx="3" fill="#fff"/><rect x="13" y="2" width="14" height="8" rx="2" fill="none" stroke="#fff" stroke-width="3"/></svg><div class="stat-big">30 Years</div><div class="stat-small">Of Experience</div></div>
    <div class="stat"><svg width="44" height="34" viewBox="0 0 44 34"><path d="M2 32V16l10-6v6l10-6v6l10-6V2h8v30z" fill="#fff"/></svg><div class="stat-big">Services For</div><div class="stat-small">Large &amp; Small Industries</div></div>
    <div class="stat"><svg width="52" height="34" viewBox="0 0 52 34"><rect x="2" y="4" width="30" height="20" fill="#fff"/><path d="M34 10h10l6 8v6H34z" fill="#fff"/><circle cx="12" cy="28" r="5" fill="#fff"/><circle cx="42" cy="28" r="5" fill="#fff"/></svg><div class="stat-big">Free Pickup &amp; Delivery</div><div class="stat-small">Within 100 Miles</div></div>
    <div class="stat"><svg width="38" height="34" viewBox="0 0 38 34"><rect x="2" y="14" width="8" height="18" fill="#fff"/><path d="M13 14l8-12c3 0 4 2 3 6l-2 5h12c2 0 3 2 2 4l-4 13H13z" fill="#fff"/></svg><div class="stat-big">100%</div><div class="stat-small">Customer Satisfaction</div></div>
  </div>
</section>

<section class="about">
  <h2 class="section-title">ABOUT US</h2>
  <p class="about-tag">Temporibus Autem Quibusdam Et Aut Officiis Debitis Aut Rerum Necessitatibus</p>
  <div class="about-copy">
    <p>Nam libero tempore, cum soluta nobis est eligendi optio cumque nihil impedit quo minus id quod maxime placeat facere possimus, omnjuklis voluptas assumenda est, omnis dolor repellendus. Temporibus autemb quibusdam et aut officiis debitis aut rerum necessitatibus saepe eveniet ut et voluptates repudiandae sint et molestiae non recusandae.</p>
    <p>Temporibus autem quibusdam et aut officiis debitis aut rerum necess itatibus saepe eveniet ut et voluptates repudiandae sint et molestiae non recusandae.</p>
    <a class="btn" href="#"><span class="btn-label">READ MORE</span><span class="btn-arrow"><svg width="18" height="18" viewBox="0 0 18 18"><circle cx="9" cy="9" r="9" fill="#ec1f27"/><path d="M7 5l4 4-4 4" stroke="#fff" stroke-width="2" fill="none"/></svg></span></a>
  </div>
  <div class="about-photo" role="img" aria-label="Technician in orange overalls servicing a hydraulic pump among yellow pipework"></div>
</section>

<section class="testimonials">
  <h2 class="section-title">TESTIMONIALS</h2>
  <svg class="slide-arrow prev" width="28" height="56" viewBox="0 0 28 56"><path d="M26 2L2 28l24 26" stroke="#888" stroke-width="2" fill="none"/></svg>
  <article class="quote-card left">
    <div class="quote-badge">“</div>
    <p class="quote-text">Nemo enim ipsam voluptatem quia voluptas sit aspe rnatur aut odit aut fugit, sed quia consequuntur magni dolores eos qui ratione volupta nesciunt.</p>
    <p class="quote-name">- Abigail</p>
  </article>
  <article class="quote-card right">
    <div class="quote-badge">“</div>
    <p class="quote-text">Nemo enim ipsam voluptatem quia voluptas sit aspe rnatur aut odit aut fugit, sed quia consequuntur magni dolores eos qui ratione volupta nesciunt.</p>
    <p class="quote-name">- Abigail</p>
  </article>
  <svg class="slide-arrow next" width="28" height="56" viewBox="0 0 28 56"><path d="M2 2l24 26L2 54" stroke="#888" stroke-width="2" fill="none"/></svg>
</section>

<section class="newsletter" role="img" aria-label="Interior of a large industrial workshop hall">
  <div class="newsletter-shade"></div>
  <div class="newsletter-box">
    <div class="mail-badge"><span><svg width="38" height="28" viewBox="0 0 38 28"><rect width="38" height="28" rx="2" fill="#fff"/><path d="M2 3l17 13L36 3" stroke="#ec1f27" stroke-width="3" fill="none"/></svg></span></div>
    <h2 class="newsletter-title">SUBSCRIBE TO OUR NEWSLETTER</h2>
    <div class="newsletter-form">
      <span class="newsletter-input">Enter Your Email Id</span>
      <span class="newsletter-submit">SUBMIT <svg width="18" height="18" viewBox="0 0 18 18"><circle cx="9" cy="9" r="9" fill="#ec1f27"/><path d="M7 5l4 4-4 4" stroke="#fff" stroke-width="2" fill="none"/></svg></span>
    </div>
    <div class="newsletter-check"><svg width="14" height="14" viewBox="0 0 14 14"><rect x="1" y="1" width="12" height="12" fill="none" stroke="#ec1f27" stroke-width="2"/><path d="M3 7l3 3 6-7" stroke="#ec1f27" stroke-width="2" fill="none"/></svg>DAILY NEWSLETTER</div>
  </div>
</section>

<footer class="site-footer">
  <div class="footer-brand"><span class="brand-dot"></span><span class="brand-name">BRACKENFORD FLUIDWORKS</span></div>
  <div class="footer-col col-links"><h3>QUICK LINKS</h3><ul><li>Home</li><li>About Us</li><li>Services</li><li>Projects</li><li>Blog</li><li>Contact</li></ul></div>
  <div class="footer-col col-res"><h3>RESOURCES</h3><ul><li>Terms</li><li>Conditions</li><li>Privacy Policy</li><li>Customer Support</li></ul></div>
  <div class="footer-col col-connect"><h3>CONNECT WITH US</h3><div class="socials"><span></span><span></span><span></span></div></div>
</footer>
<div class="copyright">Copyright © 2018. All Rights Reserved.</div>

</body>
</html>
```